Auto Body Shops Needs Email Signature Design

We are looking to update our email signature. The design needs to be easy to copy and paste into Microsoft Outlook and be editable for multiple positions.

Our company is called Dellwyn Collision & Autoglass, but we have a charity program called Dellwyn Helps Young Ones. We would like to use this logo.

Information that needs to be included:

"We Care"
Name
Title
Location
Address
Phone
Email
Cell
Fax

Our new corporate colors are gray/silver and black. We are getting away from blue (currently used).

The "Dellwyn" and "Helps Young" should be in black as they will be on a white background (comp screen).

Colors
fde1e1

Requirements
Must have
• Easily editable so it can be used as a template.
Should not have
• Main color should not be red.

```html
<!DOCTYPE html>
<html lang="en">
<head>
<meta charset="utf-8">
<title>Dellwyn Email Signature</title>
<link rel="stylesheet" href="https://fonts.googleapis.com/css2?family=Roboto+Slab:wght@300;400;700&family=Roboto:wght@400&display=swap">
<style>
  :root {
    --bg: #ffffff;
    --accent: #e8324a;
    --ink: #2b2b2b;
    --muted: #6f6f6f;
    --link: #1a1ae6;
    --logo-ink: #111111;
  }
  * { margin: 0; padding: 0; box-sizing: border-box; }
  html, body { width: 1200px; height: 719px; overflow: hidden; background: var(--bg); }
  .signature {
    position: absolute; left: 150px; top: 70px; width: 900px;
    font-family: "Roboto Slab", serif; color: var(--ink);
  }
  .tagline { color: var(--accent); font-weight: 700; font-size: 26px; margin-bottom: 40px; }
  .person-name { font-weight: 700; font-size: 36px; margin-bottom: 18px; }
  .role-line { font-weight: 300; font-size: 22px; color: var(--muted); margin-bottom: 14px; }
  .role-line a { color: var(--link); font-weight: 400; }
  .contact-line { display: flex; align-items: center; gap: 10px; font-family: "Roboto", sans-serif; font-size: 22px; color: var(--ink); margin-bottom: 14px; }
  .contact-item { display: inline-flex; align-items: center; gap: 6px; margin-right: 16px; }
  .contact-item svg { width: 20px; height: 20px; }
  .program-name { display: flex; align-items: center; gap: 10px; font-weight: 700; font-size: 30px; color: var(--logo-ink); margin-bottom: 10px; }
  .program-dot { width: 16px; height: 16px; border-radius: 50%; background: var(--accent); }
  .site-link { display: block; font-size: 22px; color: var(--accent); margin-bottom: 34px; }
  .disclaimer { font-family: "Roboto", sans-serif; font-size: 16px; line-height: 1.5; color: var(--ink); width: 640px; }
</style>
</head>
<body>
  <main class="signature">
    <p class="tagline">We Care</p>
    <h1 class="person-name">Your Name</h1>
    <p class="role-line">Regional Manager | H.O. Brentfield | <a href="mailto:email@dellwyn.com">email@dellwyn.com</a></p>
    <p class="contact-line">
      <span class="contact-item">
        <svg viewBox="0 0 20 20" aria-label="Phone"><rect x="5" y="1" width="10" height="18" rx="2" fill="var(--accent)"/><rect x="7" y="3" width="6" height="11" fill="#fff"/></svg>
        604-555-0147
      </span>
      <span class="contact-item">
        <svg viewBox="0 0 20 20" aria-label="Fax"><rect x="5" y="2" width="10" height="6" fill="none" stroke="var(--accent)" stroke-width="2"/><rect x="2" y="8" width="16" height="9" rx="1.5" fill="var(--accent)"/><rect x="6" y="12" width="8" height="2" fill="#fff"/></svg>
        604-555-0147
      </span>
    </p>
    <p class="program-name"><span class="program-dot"></span>Dellwyn Helps Young Ones</p>
    <a class="site-link" href="http://www.dellwyn-autoglass.com/">http://www.dellwyn-autoglass.com/</a>
    <p class="disclaimer">This e-mail and any attachments may contain confidential information. It is intended for the addressee(s) names herein. If you are not the intended recipient of this e-mail you are notified that any dissemination, distribution or duplication of this email and attachments is strictly prohibited. If you received this e-mail in error, please notify me immediately and permanently delete / dispose of the original and any copy of the email, attachments and any printed copies.</p>
  </main>
</body>
</html>
```